Real Estate Webpage Design

We have an existing website: ferndaleestatecollective.com.au
We focus customised service mainly on Property Management and second-hand property sales.
We are not entirely happy about the current design and layout can stay roughly the same as the back end coding is linked to a CRM system.
We would like to see the design are more reachable to our clients and appearing.
Please check our Website Design Draft for more details.

Industry/Entity Type

Real estate Agency

Number of Pages Required

5+ page

Font styles to use
Sans Serif

Colors

Designer to choose colors to be used in the design.

```html
<!DOCTYPE html>
<html lang="en">
<head>
<meta charset="utf-8">
<title>Ferndale Estate Collective</title>
<link rel="stylesheet" href="https://fonts.googleapis.com/css2?family=Lato:ital,wght@0,400;0,700;1,400&family=Montserrat:wght@400;600&family=Oswald:wght@400;500&display=swap">
<style>
:root{
  --gold:#eebf5a;
  --gold-pale:#fdf6e8;
  --ink:#1f1f1f;
  --text:#4a4a4a;
  --grey-band:#f2f2f2;
  --footer:#1c1c1c;
  --footer-text:#c9c9c9;
  --white:#ffffff;
}
*{box-sizing:border-box;margin:0;padding:0}
html,body{width:1200px;height:3662px;overflow:hidden;background:var(--white)}
body{position:relative;font-family:'Lato',sans-serif;color:var(--text)}
.heading{font-family:'Oswald',sans-serif;font-weight:400;color:var(--ink);letter-spacing:.5px}
.btn{position:absolute;background:var(--gold);color:var(--white);font:700 13px 'Lato',sans-serif;letter-spacing:.5px;display:flex;align-items:center;justify-content:center;text-transform:uppercase}

/* header */
.site-header{position:absolute;left:0;top:0;width:1200px;height:95px;background:var(--white)}
.brand{position:absolute;left:74px;top:24px;display:flex;align-items:center;gap:12px}
.brand-mark{width:44px;height:44px;background:var(--gold)}
.brand-name{font:700 30px 'Lato',sans-serif;color:var(--ink);line-height:1}
.brand-sub{font:400 11px 'Lato',sans-serif;color:var(--ink);margin-top:3px}
.main-nav{position:absolute;top:28px;left:388px;display:flex;height:36px;align-items:center;font:700 12.5px 'Lato',sans-serif;color:var(--ink)}
.main-nav span{margin-right:34px}
.main-nav .active{background:var(--gold);color:var(--white);padding:11px 16px;margin-right:22px}

/* hero */
.hero{position:absolute;left:0;top:95px;width:1200px;height:632px;background:linear-gradient(180deg,#8aa0c0 0%,#b8c2cc 30%,#c9ccd0 50%,#7b8f58 75%,#4f6a33 100%)}
.hero-title{position:absolute;top:200px;width:1200px;text-align:center;font:700 44px/60px 'Lato',sans-serif;color:var(--white);text-shadow:0 2px 6px rgba(0,0,0,.35)}
.hero-sub{position:absolute;top:262px;width:1200px;text-align:center;font:400 30px/40px 'Lato',sans-serif;color:var(--white);text-shadow:0 2px 6px rgba(0,0,0,.35)}
.dots{position:absolute;display:flex;gap:11px}
.dots i{width:11px;height:11px;border-radius:50%;background:var(--white);display:block}
.dots i.on{background:var(--gold)}

/* welcome */
.frame-pale{position:absolute;background:var(--gold-pale)}
.photo{position:absolute}
.welcome-title{position:absolute;left:614px;top:868px;font-size:39px;line-height:56px}
.welcome-copy{position:absolute;left:614px;top:935px;width:505px;font-size:16px;line-height:27.6px}
.welcome-copy p{margin-bottom:12px}

/* listings */
.band-grey{position:absolute;left:0;top:1420px;width:1200px;height:922px;background:var(--grey-band)}
.section-title{position:absolute;width:1200px;text-align:center;font-size:40px}
.tabs{position:absolute;top:1542px;width:1200px;display:flex;justify-content:center;gap:46px;font:400 18px 'Oswald',sans-serif;color:var(--ink)}
.tabs .active{color:var(--gold);text-decoration:underline;text-underline-offset:4px}
.listing-title{position:absolute;font-size:35px;top:1922px}
.listing-addr{position:absolute;font:400 24px 'Montserrat',sans-serif;color:var(--ink);top:1975px}
.listing-price{position:absolute;font:600 25px 'Montserrat',sans-serif;color:var(--ink);letter-spacing:1px;top:2018px}
.feature{position:absolute;display:flex;align-items:center;gap:14px;font:700 17px 'Lato',sans-serif;color:var(--ink)}
.feature .ico{width:40px;height:40px;border-radius:50%;background:#dcdcdc;display:flex;align-items:center;justify-content:center}
.arrow{position:absolute}

/* testimonials */
.testimonial{position:absolute;left:74px;top:2211px;width:1052px;height:402px;background:linear-gradient(135deg,#5a5e66 0%,#6e6a68 45%,#3f4652 100%)}
.testimonial .section-title{width:1052px;color:var(--white);top:78px;font-size:38px}
.quote{position:absolute;top:140px;width:1052px;text-align:center;font:italic 400 20px/34px 'Lato',sans-serif;color:var(--white)}
.quote-name{position:absolute;top:232px;width:1052px;text-align:center;font:700 16px 'Lato',sans-serif;color:var(--gold)}

/* blog */
.post-title{position:absolute;top:3008px;width:505px;font-size:30px;letter-spacing:0;white-space:nowrap;line-height:40px}
.post-copy{position:absolute;top:3060px;width:500px;font-size:14px;line-height:24px}

/* footer */
.site-footer{position:absolute;left:0;top:3277px;width:1200px;height:385px;background:var(--footer);color:var(--footer-text)}
.foot-col{position:absolute;top:48px;font-size:13.5px}
.foot-col h4{font:400 19px 'Oswald',sans-serif;color:var(--white);margin-bottom:22px}
.foot-col li{list-style:none;line-height:26px}
.contact-line{display:flex;gap:18px;align-items:center;line-height:28px}
.contact-line svg{flex:0 0 12px}
.email-input{width:243px;height:32px;border:1px solid #bdbdbd;color:var(--white);font-size:12.5px;padding:8px 14px}
.socials{position:absolute;left:882px;top:240px;display:flex;gap:24px}
.socials i{display:block;width:18px;height:18px;background:#d8d8d8}
.footer-rule{position:absolute;left:75px;top:315px;width:1050px;height:1px;background:#333}
.copyright{position:absolute;top:344px;width:1200px;text-align:center;font-size:11px;color:#a9a9a9}
</style>
</head>
<body>

<header class="site-header">
  <div class="brand">
    <div class="brand-mark"></div>
    <div>
      <div class="brand-name">Ferndale</div>
      <div class="brand-sub">Estate Collective</div>
    </div>
  </div>
  <nav class="main-nav">
    <span class="active">HOME</span><span>ABOUT US</span><span>LEASING</span><span>BUY</span><span>SELL</span><span>OUR TEAM</span><span>BLOG</span><span>CONTACT US</span><span>EN &#709;</span>
  </nav>
</header>

<section class="hero" role="img" aria-label="Modern two-storey white house with timber cladding and garden under a blue sky">
  <h1 class="hero-title">FERNDALE – A HOME WITH DEEP ROOTS</h1>
  <p class="hero-sub">Ferndale is a real estate company located<br>in Gungahlin, Canberra.</p>
  <div class="btn" style="left:528px;top:381px;width:143px;height:38px">Read More</div>
  <div class="dots" style="left:563px;top:567px"><i class="on"></i><i></i><i></i><i></i></div>
</section>

<section>
  <div class="frame-pale" style="left:60px;top:789px;width:270px;height:256px"></div>
  <div class="frame-pale" style="left:487px;top:1230px;width:120px;height:110px"></div>
  <div class="photo" role="img" aria-label="White modern pavilion with glass walls beside a pool" style="left:95px;top:825px;width:492px;height:495px;background:linear-gradient(180deg,#7fb0df 0%,#cfe0ee 35%,#e9e9e6 60%,#cfcfcb 82%,#3aa7b4 100%)"></div>
  <h2 class="heading welcome-title">WELCOME TO OUR WEBSITE</h2>
  <div class="welcome-copy">
    <p>Ferndale takes its name from the valley homes we grew up in; buying a property is one of the most expensive expenses and important assets for people. Ferndale is a real estate company located in Gungahlin, Canberra.</p>
    <p>Being a portfolio sales agent and property manager, coupled with our high–profile international real estate experience, Ferndale is considered a market leader on the cutting edge with deep industry knowledge, ranging from landlord–tenant relationships, residential purchases.</p>
  </div>
  <div class="btn" style="left:614px;top:1226px;width:143px;height:38px;opacity:.7">Read More</div>
</section>

<div class="band-grey"></div>
<h2 class="heading section-title" style="top:1468px">THIS MONTH AT FERNDALE ESTATE COLLECTIVE</h2>
<div class="tabs"><span class="active">FOR SALE</span><span>FOR LEASE</span><span>OPEN TIMES</span><span>SOLD</span><span>LEASED</span></div>

<svg class="arrow" style="left:38px;top:1853px" width="22" height="36" viewBox="0 0 22 36"><path d="M19 2 3 18l16 16" fill="none" stroke="#222" stroke-width="2.5"/></svg>
<svg class="arrow" style="left:1140px;top:1853px" width="22" height="36" viewBox="0 0 22 36"><path d="M3 2l16 16L3 34" fill="none" stroke="#222" stroke-width="2.5"/></svg>

<div class="photo" role="img" aria-label="Curved high-rise apartment tower against a cloudy sky" style="left:76px;top:1604px;width:511px;height:289px;background:linear-gradient(180deg,#9ec3e6 0%,#d7e3ee 50%,#b9b9b6 100%)"></div>
<div class="photo" role="img" aria-label="Apartment blocks with pink balconies and a tree" style="left:614px;top:1604px;width:511px;height:289px;background:linear-gradient(180deg,#3f86d8 0%,#a8c9ea 40%,#d9d7d2 70%,#4d5a3a 100%)"></div>

<h3 class="heading listing-title" style="left:74px">GUNGAHLIN</h3>
<div class="listing-addr" style="left:74px">Level 5/20 Kestrel Crescent</div>
<div class="listing-price" style="left:74px">$500,000+</div>
<h3 class="heading listing-title" style="left:612px">BELCONNEN</h3>
<div class="listing-addr" style="left:612px">172/9 Banksia Row, Belco</div>
<div class="listing-price" style="left:612px">$369,900+</div>

<div class="feature" style="left:524px;top:1930px"><span class="ico"><svg width="18" height="12" viewBox="0 0 18 12"><path d="M1 1v10M1 7h16v4M4 4h5v3H4z" stroke="#333" stroke-width="2" fill="none"/></svg></span>2</div>
<div class="feature" style="left:524px;top:1986px"><span class="ico"><svg width="18" height="14" viewBox="0 0 18 14"><path d="M1 6h16v3a4 4 0 0 1-4 4H5a4 4 0 0 1-4-4zM3 6V2h3" stroke="#333" stroke-width="2" fill="none"/></svg></span>2</div>
<div class="feature" style="left:524px;top:2042px"><span class="ico"><svg width="18" height="14" viewBox="0 0 18 14"><path d="M2 7l2-5h10l2 5v5H2z" fill="#333"/></svg></span>1</div>
<div class="feature" style="left:1062px;top:1930px"><span class="ico"><svg width="18" height="12" viewBox="0 0 18 12"><path d="M1 1v10M1 7h16v4M4 4h5v3H4z" stroke="#333" stroke-width="2" fill="none"/></svg></span>1</div>
<div class="feature" style="left:1062px;top:1986px"><span class="ico"><svg width="18" height="14" viewBox="0 0 18 14"><path d="M1 6h16v3a4 4 0 0 1-4 4H5a4 4 0 0 1-4-4zM3 6V2h3" stroke="#333" stroke-width="2" fill="none"/></svg></span>1</div>
<div class="feature" style="left:1062px;top:2042px"><span class="ico"><svg width="18" height="14" viewBox="0 0 18 14"><path d="M2 7l2-5h10l2 5v5H2z" fill="#333"/></svg></span>1</div>

<div class="btn" style="left:75px;top:2096px;width:143px;height:39px">More Info</div>
<div class="btn" style="left:614px;top:2096px;width:143px;height:39px">More Info</div>

<section class="testimonial" role="img" aria-label="Happy family relaxing together on a sofa at home">
  <h2 class="heading section-title">TESTIMONIALS</h2>
  <p class="quote">Marnie is my best property manager! Always happy to response my queries and keep us well<br>informed at all stage. I will definitely recommend her to my friends.</p>
  <div class="quote-name">LIN HAVERS</div>
  <div class="dots" style="left:482px;top:314px;gap:14px"><i></i><i class="on"></i><i class="on"></i><i class="on"></i></div>
</section>

<h2 class="heading section-title" style="top:2655px">BLOG POSTS</h2>
<div class="photo" role="img" aria-label="Apartment complex with landscaped courtyard" style="left:76px;top:2744px;width:511px;height:229px;background:linear-gradient(180deg,#2f6fd0 0%,#9fc2e8 40%,#dcdcd8 70%,#6c8a4a 100%)"></div>
<div class="photo" role="img" aria-label="Bright open-plan living room with grey sofa" style="left:615px;top:2744px;width:511px;height:229px;background:linear-gradient(180deg,#e9e9e7 0%,#d6d4cf 55%,#8d8c88 100%)"></div>

<h3 class="heading post-title" style="left:74px">CURABITUR TEMPUS NUNC NON PULVINAR</h3>
<p class="post-copy" style="left:76px">Aenean consequat, risus nec pretium sagittis, turpis enim tempor ipsum, ac mattis leo odio in leo. Pellentesque vestibulum rutrum lacus ut condimentum. Vestibulum ante ipsum primis in faucibus orci luctus et ultrices posuere cubilia</p>
<h3 class="heading post-title" style="left:613px">CURABITUR TEMPUS NUNC NON PULVINAR</h3>
<p class="post-copy" style="left:615px">Aenean consequat, risus nec pretium sagittis, turpis enim tempor ipsum, ac mattis leo odio in leo. Pellentesque vestibulum rutrum lacus ut condimentum. Vestibulum ante ipsum primis in faucibus orci luctus et ultrices posuere cubilia</p>
<div class="btn" style="left:75px;top:3177px;width:143px;height:39px">Read More</div>
<div class="btn" style="left:614px;top:3177px;width:143px;height:39px">Read More</div>

<footer class="site-footer">
  <div class="foot-col" style="left:75px">
    <h4>COMPANY</h4>
    <ul><li>Home</li><li>About Us</li><li>Services</li><li>Gallery</li><li>Testimonials</li><li>Blog</li><li>Contact</li></ul>
  </div>
  <div class="foot-col" style="left:290px;width:230px">
    <h4>QUICK LINKS</h4>
    <ul><li>Contact Us</li><li style="margin-top:6px">Privacy</li><li style="margin-top:6px">Complaint Handling &amp; Dispute Resolution</li><li style="margin-top:6px">Due Diligence Checklist</li><li style="margin-top:6px">Sitemap</li></ul>
  </div>
  <div class="foot-col" style="left:586px;width:260px">
    <h4>CONTACT INFORMATION</h4>
    <p style="line-height:23px;margin-bottom:4px">18/5 Wattlebird Lane,<br>Gungahlin, ACT, 2912</p>
    <div class="contact-line"><svg width="12" height="12" viewBox="0 0 12 12"><path d="M2 1l3 2-1 2a7 7 0 0 0 3 3l2-1 2 3-2 1C5 11 1 7 1 3z" fill="#ccc"/></svg>02 6100 0000</div>
    <div class="contact-line"><svg width="12" height="12" viewBox="0 0 12 12"><rect x="1" y="4" width="10" height="7" fill="#ccc"/><rect x="3" y="1" width="6" height="3" fill="#ccc"/></svg>02 6100 0000</div>
    <div class="contact-line"><svg width="12" height="10" viewBox="0 0 12 10"><rect x="0" y="0" width="12" height="10" fill="#ccc"/><path d="M0 0l6 5 6-5" stroke="#1c1c1c" fill="none"/></svg>hello@ferndaleestate.com</div>
    <div class="contact-line"><svg width="12" height="14" viewBox="0 0 12 14"><path d="M6 14S1 8 1 5a5 5 0 0 1 10 0c0 3-5 9-5 9z" fill="#ccc"/><circle cx="6" cy="5" r="2" fill="#1c1c1c"/></svg>Map Direction</div>
  </div>
  <div class="foot-col" style="left:882px">
    <h4>EMAIL SIGN UP</h4>
    <div class="email-input">Email Address</div>
  </div>
  <div class="btn" style="left:1050px;top:153px;width:76px;height:36px">Send</div>
  <div class="socials"><i></i><i></i><i></i><i></i><i></i></div>
  <div class="footer-rule"></div>
  <div class="copyright">Copyright © 2022 Ferndale Estate Collective. All Right Reserved</div>
</footer>

</body>
</html>
```